Private Investigation Business Card Design

I need a business card for a new private investigation company named Brisk Inquiries. I perform mainly surveillance jobs, vehicle repossessions, document serves etc. The final design should aim for a professional look. The logo has a magnifying glass with stick man arms and legs and is in a running action to show the "Brisk" aspect of the name. If the colour scheme could remain the same as the website www.briskinquiries-demo.com.au with silvers,blacks and a couple electric blue highlights.
Industry/Entity Type
Business
Contact Information for Business Card
Morgan Kellaway
Brisk Inquiries
0487316204
PO Box 58, Carnwell NSW 2291
info@briskinquiries-demo.com.au
www.briskinquiries-demo.com.au
Look and feel

```html
<!DOCTYPE html>
<html lang="en">
<head>
<meta charset="utf-8">
<title>Brisk Inquiries — Business Card</title>
<link href="https://fonts.googleapis.com/css2?family=Source+Sans+3:wght@400;600;700&display=swap" rel="stylesheet">
<style>
  :root {
    --backdrop: #000000;
    --card: #38383b;
    --card-edge: #2f2f32;
    --ink: #f2f2f2;
    --ink-soft: #d9d9d9;
    --silver: #c9c9cc;
    --divider: rgba(255,255,255,0.08);
  }
  * { margin: 0; padding: 0; box-sizing: border-box; }
  html, body {
    width: 1200px; height: 900px; overflow: hidden;
    background: var(--backdrop);
    font-family: "Source Sans 3", "Myriad Pro", Arial, sans-serif;
  }
  .stage { position: relative; width: 1200px; height: 900px; }
  .card {
    position: absolute; top: 271px;
    width: 457px; height: 281px;
    border-radius: 12px;
    background: linear-gradient(180deg, var(--card) 0%, var(--card-edge) 100%);
  }
  .card--front { left: 137px; }
  .card--back { left: 626px; }

  .brand-mark {
    position: absolute; display: flex; align-items: center; gap: 10px;
    color: var(--silver); font-weight: 700;
  }
  .card--front .brand-mark { left: 42px; top: 118px; font-size: 30px; }
  .brand-mark .dot {
    width: 34px; height: 34px; border-radius: 50%;
    background: var(--silver);
  }
  .card--back .brand-mark {
    left: 0; right: 0; top: 0; bottom: 0; justify-content: center;
    font-size: 42px; letter-spacing: 0.5px;
  }
  .card--back .brand-mark .dot { width: 40px; height: 40px; }

  .divider {
    position: absolute; left: 210px; top: 40px;
    width: 1px; height: 200px; background: var(--divider);
  }
  .details { position: absolute; left: 228px; top: 59px; color: var(--ink-soft); font-size: 13px; line-height: 18px; }
  .details .name { color: var(--ink); font-size: 15.5px; font-weight: 600; line-height: 20px; }
  .details .company { margin-bottom: 21px; }
  .details .address { margin-bottom: 16px; }
  .contact { list-style: none; }
  .contact li { display: flex; align-items: center; gap: 7px; line-height: 19px; }
  .contact svg { width: 9px; height: 9px; fill: var(--ink-soft); flex: none; }
</style>
</head>
<body>
<main class="stage">
  <section class="card card--front" aria-label="Card front">
    <div class="brand-mark"><span class="dot"></span>Brisk</div>
    <div class="divider"></div>
    <div class="details">
      <p class="name">Morgan Kellaway</p>
      <p class="company">Brisk Inquiries</p>
      <p class="address">PO Box 58, Carnwell<br>NSW 2291</p>
      <ul class="contact">
        <li><svg viewBox="0 0 10 10"><path d="M1 3.5C1 2 2 1.5 5 1.5S9 2 9 3.5L7.5 4 7 3H3L2.5 4ZM2.5 5h5l1 3.5h-7Z"/></svg>0487316204</li>
        <li><svg viewBox="0 0 10 10"><path d="M1 2h8v1L5 5.5 1 3Zm0 2 4 2.5L9 4v4H1Z"/></svg>info@briskinquiries-demo.com.au</li>
        <li><svg viewBox="0 0 10 10"><path d="M4 6 6 4M3.5 4.5 2 6a1.4 1.4 0 0 0 2 2l1.5-1.5M6.5 5.5 8 4a1.4 1.4 0 0 0-2-2L4.5 3.5" stroke="#d9d9d9" stroke-width="1.1" fill="none"/></svg>www.briskinquiries-demo.com.au</li>
      </ul>
    </div>
  </section>

  <section class="card card--back" aria-label="Card back">
    <div class="brand-mark">Brisk Inquiries<span class="dot"></span></div>
  </section>
</main>
</body>
</html>
```